Market Research firm needs updated business cards with new logo

We need the logo to be included somewhere on the card (attached). We would also like the phrases "Independent, Objective, Comprehensive" and "Research You Can Trust" somewhere on the card. Front or back. Our colors are hex codes 6075a7, e48d25 and 5a5b5b. Though you are certainly not limited to those shades, whatever you produce should coordinate with them. I have also attached our favicon. Feel free to use it in your design, but please do not use it to replace the full logo.

Contact Information for Business Card

see project description

Font styles to use
Other font styles liked:
• Open Sans

Requirements
Must have
• the logo
• We use Open Sans font

```html
<!DOCTYPE html>
<html lang="en">
<head>
<meta charset="utf-8">
<title>Norvale Research – Business Card</title>
<link rel="stylesheet" href="https://fonts.googleapis.com/css2?family=Open+Sans:wght@400;600;700&family=Roboto:wght@400;700&display=swap">
<style>
  :root {
    --blue: #6075a7;
    --orange: #e48d25;
    --grey: #5a5b5b;
    --white: #ffffff;
    --stage: #000000;
  }
  * { margin: 0; padding: 0; box-sizing: border-box; }
  html, body { width: 1200px; height: 1200px; overflow: hidden; background: var(--stage); }
  .stage { position: relative; width: 1200px; height: 1200px; }
  .card {
    position: absolute; left: 180px; width: 840px; height: 480px;
    background: var(--white); overflow: hidden;
    font-family: "Roboto", "Open Sans", sans-serif;
  }
  .card--front { top: 98px; }
  .card--back { top: 622px; }

  .brand {
    position: absolute; display: flex; align-items: center; gap: 12px;
    font-family: "Open Sans", sans-serif; font-weight: 600; color: var(--blue);
    white-space: nowrap; letter-spacing: -0.5px;
  }
  .brand__dot { border-radius: 50%; background: var(--orange); flex: none; }
  .card--front .brand { right: 20px; top: 60px; font-size: 46px; }
  .card--front .brand__dot { width: 34px; height: 34px; }
  .card--back .brand { left: 0; right: 0; justify-content: center; top: 172px; font-size: 70px; }
  .card--back .brand__dot { width: 50px; height: 50px; }

  .holder { position: absolute; left: 36px; top: 262px; color: var(--grey); }
  .holder__name { font-weight: 700; font-size: 40px; line-height: 1; letter-spacing: 0.5px; }
  .holder__role { font-size: 28px; line-height: 1; margin-top: 4px; }
  .divider {
    position: absolute; left: 128px; right: 0; top: 318px;
    border-top: 2px dotted var(--orange); opacity: 0.8;
  }

  .contact { position: absolute; display: flex; align-items: center; gap: 6px; color: var(--orange); }
  .contact svg { flex: none; }
  .contact--phone { left: 26px; top: 344px; font-size: 29px; }
  .contact--email { left: 28px; top: 392px; font-size: 23px; }
  .contact--place { left: 578px; top: 336px; font-size: 23px; line-height: 1.15; align-items: flex-start; gap: 14px; }

  .footer-bands { position: absolute; left: 0; top: 420px; }
  .website {
    position: absolute; left: 566px; top: 433px; font-size: 30px; color: var(--orange);
  }

  .taglines { position: absolute; top: 296px; left: 0; width: 100%; }
  .tagline {
    position: absolute; font-weight: 700; font-size: 22px; color: var(--orange);
    letter-spacing: 0.2px; white-space: nowrap;
  }
  .tagline--independent { left: 46px; }
  .tagline--comprehensive { left: 236px; }
  .tagline--trust { left: 478px; }
</style>
</head>
<body>
<main class="stage">

  <section class="card card--front">
    <div class="brand"><span class="brand__dot"></span>Norvale Research</div>

    <div class="holder">
      <p class="holder__name">JOHN SMITH</p>
      <p class="holder__role">Owner</p>
    </div>
    <div class="divider"></div>

    <p class="contact contact--phone">
      <svg width="26" height="26" viewBox="0 0 26 26" aria-hidden="true">
        <circle cx="13" cy="13" r="13" fill="var(--orange)"/>
        <path d="M8.5 7.5c1-.8 1.8-.6 2.3.3l1 1.9c.3.7.1 1.2-.5 1.6l-.7.5c.6 1.6 1.8 2.9 3.4 3.6l.5-.7c.4-.6 1-.8 1.6-.5l1.9 1c.9.5 1 1.3.3 2.2-1 1.2-2.6 1.4-4.6.4-2.8-1.4-4.8-3.7-5.8-6.3-.6-1.7-.4-3 .6-4z" fill="#fff"/>
      </svg>
      455 555 555
    </p>

    <p class="contact contact--email">
      <svg width="30" height="22" viewBox="0 0 30 22" aria-hidden="true">
        <rect x="1" y="1" width="28" height="20" fill="none" stroke="var(--orange)" stroke-width="2"/>
        <path d="M1 1l14 11L29 1M1 21l10-10M29 21L19 11" fill="none" stroke="var(--orange)" stroke-width="2"/>
      </svg>
      youremail@gmail.com
    </p>

    <p class="contact contact--place">
      <svg width="22" height="32" viewBox="0 0 22 32" aria-hidden="true" style="margin-top:8px">
        <path d="M11 0C4.9 0 0 4.9 0 11c0 7.5 11 21 11 21s11-13.5 11-21C22 4.9 17.1 0 11 0z" fill="var(--orange)"/>
        <circle cx="11" cy="11" r="4.5" fill="#fff"/>
      </svg>
      <span>your location and<br>zip address</span>
    </p>

    <svg class="footer-bands" width="840" height="60" viewBox="0 0 840 60" aria-hidden="true">
      <path d="M0 17h538a6 6 0 0 1-6 9H0z" fill="var(--grey)"/>
      <path d="M0 34h540l8-25a12 12 0 0 1 10-8h282v59H0z" fill="var(--blue)"/>
    </svg>
    <p class="website">www.yourweb.com</p>
  </section>

  <section class="card card--back">
    <div class="brand"><span class="brand__dot"></span>Norvale Research</div>
    <div class="taglines">
      <span class="tagline tagline--independent">INDEPENDENT</span>
      <span class="tagline tagline--comprehensive">COMPREHENSIVE</span>
      <span class="tagline tagline--trust">RESEARCH YOU CAN TRUST</span>
    </div>
  </section>

</main>
</body>
</html>
```